Tuition Center Website

We need a new web site for a tutoring company based in sydney.

We only teach senior highschool students and pride ourselves on building the students abilities to think their way through life.

I would like a bright and vibrant website that looks professional and modern.
It needs to look simple and neat but also have the functionality we need.
Images and flash would be good.

Please keep in mind that the site must be appealing to a younger audience.

We need a multipage website with the following navigation bars:

1.Home (As logo not "home" button)
I would like a news box/ticker somewhere that can stream our chatterbook and pipstream feeds and also any news updates we want to put up.
Subscribe to newsletter button.

2. About us.
This needs to be a pull down into:
-What we do
-Why we do it
-How we do it

3. Courses
Pulldown into:
-Maths
-English
-Science
(we may need to attach extra pages behind these e.g. Courses/Science/Physics or Courses/Science/Chemistry and possibly add a link to a new zandlo form)

4. Inspired
This page is like a blog page where we can upload videos, links to articles that we find to be inspiring and hopefully will inspire others.

5. Inspire
This is a recruitment page. Only content here.

6. Contact us.
Mapquill map widget and a 'contact us' form

* Our branding requires green close to #12FF3D

***Please have a look at the current website.
@ www.velmorlearning.com.au

Thanks everybody hope the revision of my brief is better and more informative than my last one

Target Market(s)

senior highschool students aged 15-19, parents ( to a lesser degree)

Industry/Entity Type

It Company

Requirements
Must have
• Ability to change content on pages.

The green doesn't have to be everywhere, but it must be obvious that it is our colour.

Nice to have
• Sites with a nicer mix of images and flash will be given more consideration. But then again, if you amaze us, you amaze us and we will go with your design.
Should not have
• Should stay away from ocre, brown colours and serif fonts.

```html
<!DOCTYPE html>
<html lang="en">
<head>
<meta charset="utf-8">
<title>Velmor Learning – Senior HSC Coaching</title>
<link href="https://fonts.googleapis.com/css2?family=Signika:wght@300;400;600&family=Oswald:wght@500&display=swap" rel="stylesheet">
<style>
:root{
  --page:#ececec;
  --card:#ffffff;
  --lime:#9ed316;
  --lime-dark:#7fb800;
  --green-text:#5c9a00;
  --nav-text:#2e4a00;
  --ink:#333333;
  --muted:#8a8a8a;
  --teal:#2a9bbf;
  --dark-box:#333333;
  --rule:#e2e2e2;
}
*{margin:0;padding:0;box-sizing:border-box}
html,body{width:1200px;height:1111px;overflow:hidden}
body{background:var(--page);font-family:"Signika",sans-serif;color:var(--ink);position:relative}
.card{position:absolute;left:179px;top:34px;width:841px;height:1042px;background:var(--card);border-radius:4px;box-shadow:0 1px 4px rgba(0,0,0,.12)}
.abs{position:absolute}
/* header */
.brand{left:54px;top:30px;display:flex;align-items:center;gap:8px}
.brand-mark{width:34px;height:34px;background:var(--lime)}
.brand-name{font-size:19px;font-weight:600;color:var(--ink);line-height:1}
.call{left:652px;top:30px}
.call-text{position:absolute;left:39px;top:0;font-size:16px;font-weight:300;color:#3a4a6a;line-height:18px;white-space:nowrap}
.call-number{position:absolute;left:3px;top:38px;font-size:24px;font-weight:300;color:#222;letter-spacing:.5px;white-space:nowrap}
/* nav */
.nav{left:0;top:117px;width:841px;height:39px;background:linear-gradient(#b0e22a,var(--lime) 60%,#8cc400);border-radius:3px 3px 0 0}
.nav a{position:absolute;top:11px;font-size:13.5px;font-weight:600;color:var(--nav-text);text-decoration:none;white-space:nowrap}
.nav .sep{position:absolute;top:6px;width:1px;height:28px;background:rgba(255,255,255,.35);box-shadow:-1px 0 0 rgba(0,0,0,.08)}
.social{position:absolute;top:9px;width:21px;height:21px;border-radius:50%;border:2px solid #fff}
/* hero */
.hero{left:1px;top:156px;width:839px;height:341px;background:
  linear-gradient(90deg,rgba(0,0,0,0) 45%,rgba(40,50,40,.35) 100%),
  linear-gradient(180deg,#8fb2d6 0%,#b7c2c8 35%,#9aa09a 62%,#5d7c3c 85%,#4d7030 100%)}
.hero-copy{left:473px;top:74px;width:340px;color:#fff}
.hero-title{font-family:"Oswald",sans-serif;font-weight:500;font-size:28px;line-height:31px;text-transform:uppercase;text-shadow:0 1px 3px rgba(0,0,0,.4)}
.hero-text{margin-top:10px;font-size:13.5px;line-height:20px;text-shadow:0 1px 2px rgba(0,0,0,.5)}
.btn-enquire{display:inline-block;margin-top:15px;width:137px;height:35px;line-height:35px;text-align:center;background:linear-gradient(#ffffff,#dcdcdc);border-radius:2px;color:#333;font-size:16px;letter-spacing:.5px;box-shadow:0 1px 3px rgba(0,0,0,.3)}
/* columns */
.col-title{font-size:16px;color:#333;line-height:22px;text-transform:uppercase}
.body-text{font-size:11.5px;line-height:17px;color:var(--muted);font-weight:300}
.welcome{left:24px;top:527px;width:245px}
.welcome .body-text{margin-top:10px}
.welcome .body-text + .body-text{margin-top:9px}
.quote{margin-top:11px;font-size:11px;color:#555}
.quote b{font-weight:600;color:#333}
.news{left:296px;top:527px;width:254px}
.news-rule{position:relative;margin-top:10px;height:1px;background:var(--rule)}
.news-rule::before{content:"";position:absolute;left:0;top:-2px;width:32px;height:3px;background:#6ab6cf}
.news-item{position:relative;height:107px}
.news-item + .news-item{border-top:1px solid var(--rule)}
.date{position:absolute;left:0;top:15px;width:38px;height:44px;text-align:center}
.date-day{height:26px;background:var(--lime-dark);color:#fff;font-size:18px;line-height:26px;font-weight:600}
.date-month{height:18px;background:#3a3a3a;color:#fff;font-size:10.5px;line-height:18px}
.news-body{position:absolute;left:56px;top:13px;width:198px}
.news-name{font-size:14px;color:#444}
.news-body .body-text{font-size:10.5px;line-height:15px;margin-top:4px}
.read-more{display:inline-block;margin-top:8px;font-size:11px;font-weight:600;color:#444;text-decoration:underline}
.reviews{left:575px;top:527px;width:250px}
.review{position:relative;height:69px}
.review:first-of-type{margin-top:8px}
.avatar{position:absolute;left:0;top:0;width:53px;height:51px;border-radius:2px}
.review-name{position:absolute;left:65px;top:0;font-size:13.5px;color:var(--teal)}
.review-text{position:absolute;left:65px;top:20px;font-size:10.5px;line-height:15px;color:var(--muted)}
.divider{left:42px;top:795px;width:733px;height:1px;background:var(--rule)}
/* bottom box */
.beliefs{left:24px;top:830px;width:793px;height:192px;border:1px solid #d6d6d6;border-radius:4px;background:linear-gradient(#ffffff,#ebebeb)}
.trial-title{left:18px;top:33px;font-size:16px;font-weight:600;color:var(--green-text);text-transform:uppercase}
.trial-box{left:17px;top:57px;width:224px;height:60px;background:var(--dark-box);color:#fff;padding:9px 13px}
.trial-line1{font-size:14px;font-weight:300}
.trial-line2{text-align:right;font-size:14px;font-weight:300}
.trial-line2 strong{font-size:18px;font-weight:600;font-style:italic;color:#8fd11a}
.trial-text{left:18px;top:124px;width:230px;font-size:11px;line-height:17px;color:var(--muted);font-weight:300}
.trial-link{left:17px;top:161px;font-size:12px;color:#333}
.belief-head{font-size:20px;font-weight:400;color:var(--green-text)}
.belief-list{list-style:none}
.belief-list li{position:relative;padding-left:23px;font-size:12px;line-height:14px;color:#777;margin-bottom:10px}
.belief-list svg{position:absolute;left:0;top:0}
/* footer */
.footer-copy{left:203px;top:1087px;font-size:11px;color:#444}
.footer-nav{right:204px;top:1087px;display:flex;gap:13px}
.footer-nav a{font-size:11.5px;color:#444;text-decoration:none}
</style>
</head>
<body>
<div class="card">
  <header>
    <div class="abs brand"><span class="brand-mark"></span><span class="brand-name">Velmor Learning</span></div>
    <div class="abs call">
      <svg width="34" height="34" viewBox="0 0 34 34" fill="none" stroke="#2c3450" stroke-width="2.4">
        <path d="M5 20 V15 a12 12 0 0 1 24 0 V20"/>
        <rect x="2" y="16" width="6" height="10" rx="2" fill="#2c3450"/>
        <rect x="26" y="16" width="6" height="10" rx="2" fill="#2c3450"/>
        <path d="M29 26 q0 6 -10 6" stroke-width="1.6"/>
      </svg>
      <div class="call-text">Call for a<br>free Consultation !</div>
      <div class="call-number">555-014-2273</div>
    </div>
  </header>

  <nav class="abs nav">
    <a style="left:32px">Home</a><span class="sep" style="left:94px"></span>
    <a style="left:119px">About Us</a><span class="sep" style="left:201px"></span>
    <a style="left:225px">Courses</a><span class="sep" style="left:298px"></span>
    <a style="left:325px">Inspired</a><span class="sep" style="left:401px"></span>
    <a style="left:427px">Inspire</a><span class="sep" style="left:495px"></span>
    <a style="left:521px">Contact Us</a><span class="sep" style="left:610px"></span>
    <a style="left:637px">Follow Us</a>
    <span class="social" style="left:709px;background:#1a7ab8" aria-label="Network profile"></span>
    <span class="social" style="left:737px;background:#3a5ba8" aria-label="chatterbook"></span>
    <span class="social" style="left:765px;background:#2aa9e0" aria-label="pipstream"></span>
    <span class="social" style="left:793px;background:#f4f4f4" aria-label="Photo profile"></span>
  </nav>

  <section class="abs hero" role="img" aria-label="Photo of four smiling senior students holding books in front of a school building">
    <div class="abs hero-copy">
      <h1 class="hero-title">I am Velmor<br>Real HSC coaching<br>&amp; mentoring.</h1>
      <p class="hero-text">The HSC help you need, in the years you need it. We offer small classes, individualised attention and genuine care for each student. It's different - in a good way.</p>
      <span class="btn-enquire">ENQUIRE NOW</span>
    </div>
  </section>

  <section class="abs welcome">
    <h2 class="col-title">Welcome to<br>Velmor Learning</h2>
    <p class="body-text">Lorem ipsum dolor sit amet, consec dipiscing elit, sed diam. nonummy nibh euismodunt ut laoreet dolore magna. aliquam erat volutpat. Ut wisi enim ad minim veniam.</p>
    <p class="body-text">Quis nostrud.erci tation orper suscipit obortis. nisl ut aliquip ex commodo consequat. autem vel eum iriure dolor in rerit in vulputate velit esse molestie.</p>
    <p class="quote">“<b>Darren Okafor</b>” Hillcrest HS</p>
  </section>

  <section class="abs news">
    <h2 class="col-title">News Updates</h2>
    <div class="news-rule"></div>
    <article class="news-item">
      <div class="date"><div class="date-day">15</div><div class="date-month">Dec</div></div>
      <div class="news-body">
        <div class="news-name">Darren Okafor</div>
        <p class="body-text">Lorem ipsum dolor sit amet, consec dipiscing elit, sed diam.</p>
        <a class="read-more">Read More</a>
      </div>
    </article>
    <article class="news-item">
      <div class="date"><div class="date-day">10</div><div class="date-month">Dec</div></div>
      <div class="news-body">
        <div class="news-name">Darren Okafor</div>
        <p class="body-text">Lorem ipsum dolor sit amet, consec dipiscing elit, sed diam.</p>
        <a class="read-more">Read More</a>
      </div>
    </article>
  </section>

  <section class="abs reviews">
    <h2 class="col-title">What our student say?</h2>
    <div class="review">
      <div class="avatar" role="img" aria-label="Portrait of a student" style="background:linear-gradient(#d9a070,#8a8e96)"></div>
      <div class="review-name">Mr Tom Harlow</div>
      <div class="review-text">“Le Lorem Ipsum est simplement du<br>faux texte employé dans la”</div>
    </div>
    <div class="review">
      <div class="avatar" role="img" aria-label="Portrait of a student" style="background:linear-gradient(#e6e0da,#5a4438)"></div>
      <div class="review-name">Mr Tom Harlow</div>
      <div class="review-text">“Le Lorem Ipsum est simplement du<br>faux texte employé dans la”</div>
    </div>
    <div class="review">
      <div class="avatar" role="img" aria-label="Portrait of a parent" style="background:linear-gradient(#c8d0d8,#d8b890 55%,#2a2e3a)"></div>
      <div class="review-name">Mr Tom Harlow</div>
      <div class="review-text">“Le Lorem Ipsum est simplement du<br>faux texte employé dans la”</div>
    </div>
  </section>

  <div class="abs divider"></div>

  <section class="abs beliefs">
    <h3 class="abs trial-title">Free Trial Lesson.</h3>
    <div class="abs trial-box">
      <div class="trial-line1">Sign Up For</div>
      <div class="trial-line2"><strong>Free Trial Class</strong> today</div>
    </div>
    <p class="abs trial-text">Lorem ipsum dolor&nbsp; amet, consec dipiscing elit, sed diam.</p>
    <a class="abs trial-link">Send an Enquiry</a>

    <div class="abs" style="left:283px;top:27px;display:flex;align-items:center;gap:14px">
      <svg width="36" height="34" viewBox="0 0 36 34"><rect x="2" y="6" width="32" height="20" rx="2" fill="none" stroke="#5c9a00" stroke-width="3"/><rect x="14" y="26" width="8" height="4" fill="#5c9a00"/><rect x="9" y="30" width="18" height="3" fill="#5c9a00"/><circle cx="9" cy="8" r="6" fill="#555"/><circle cx="9" cy="8" r="2.5" fill="#fff"/></svg>
      <h4 class="belief-head">We Don't Believe In:</h4>
    </div>
    <ul class="abs belief-list" style="left:296px;top:103px;width:240px">
      <li><svg width="16" height="14" viewBox="0 0 16 14"><path d="M2 4v9h11V9" fill="none" stroke="#5c9a00" stroke-width="2"/><path d="M6 9q1-5 6-5V1l4 4-4 4V6q-4 0-6 3z" fill="#5c9a00"/></svg>Massive classes;</li>
      <li><svg width="16" height="14" viewBox="0 0 16 14"><path d="M2 4v9h11V9" fill="none" stroke="#5c9a00" stroke-width="2"/><path d="M6 9q1-5 6-5V1l4 4-4 4V6q-4 0-6 3z" fill="#5c9a00"/></svg>Spoon-feeding answers;</li>
      <li><svg width="16" height="14" viewBox="0 0 16 14"><path d="M2 4v9h11V9" fill="none" stroke="#5c9a00" stroke-width="2"/><path d="M6 9q1-5 6-5V1l4 4-4 4V6q-4 0-6 3z" fill="#5c9a00"/></svg>vOne-size-fits-all teaching.</li>
    </ul>

    <div class="abs" style="left:559px;top:27px;display:flex;align-items:center;gap:18px">
      <svg width="40" height="34" viewBox="0 0 40 34"><rect x="2" y="3" width="36" height="26" fill="none" stroke="#5c9a00" stroke-width="3"/><rect x="7" y="9" width="12" height="7" fill="#555"/><rect x="7" y="19" width="20" height="2.5" fill="#555"/><rect x="7" y="24" width="16" height="2.5" fill="#555"/><path d="M29 18l8 8-4 0 2 4-2 1-2-4-3 3z" fill="#333"/></svg>
      <h4 class="belief-head">We Do Believe In:</h4>
    </div>
    <ul class="abs belief-list" style="left:562px;top:103px;width:230px">
      <li><svg width="16" height="14" viewBox="0 0 16 14"><path d="M2 4v9h11V9" fill="none" stroke="#5c9a00" stroke-width="2"/><path d="M6 9q1-5 6-5V1l4 4-4 4V6q-4 0-6 3z" fill="#5c9a00"/></svg>Small classes tailored to you;</li>
      <li><svg width="16" height="14" viewBox="0 0 16 14"><path d="M2 4v9h11V9" fill="none" stroke="#5c9a00" stroke-width="2"/><path d="M6 9q1-5 6-5V1l4 4-4 4V6q-4 0-6 3z" fill="#5c9a00"/></svg>Helping you think for yourself;</li>
      <li><svg width="16" height="14" viewBox="0 0 16 14"><path d="M2 4v9h11V9" fill="none" stroke="#5c9a00" stroke-width="2"/><path d="M6 9q1-5 6-5V1l4 4-4 4V6q-4 0-6 3z" fill="#5c9a00"/></svg>Genuinely caring about who you are as an individual.</li>
    </ul>
  </section>
</div>

<footer>
  <div class="abs footer-copy">© Velmor Learning. All rights reserved.</div>
  <nav class="abs footer-nav"><a>Home</a><a>About Us</a><a>Courses</a><a>Inspired</a><a>Inspire</a><a>Contact Us</a></nav>
</footer>
</body>
</html>
```